Harbor Ledger Funds Bus card and Logo

I need a logo design and Bus card design. The fund focuses on evaluating and investing in minerals (sub-surface rights) and real estate.

Harbor ledger refers to a book of knowledge that each plebe gets when entering the Kelmont Marine Academy (my alma mater)

Target Market(s)

Investors and financial advisors

Contact Information for Business Card

Simple - perhaps a logo with a theme on book of knowledge

Logo Text

Ex Scientia Imperium

Font styles to use
Serif
Sans Serif

Colors

Designer to choose colors to be used in the design.

Requirements
Must have
• memorable logo that is relatively simple

```html
<!DOCTYPE html>
<html lang="en">
<head>
<meta charset="utf-8">
<title>Harbor Ledger Funds – Business Card</title>
<link href="https://fonts.googleapis.com/css2?family=Montserrat:wght@600&family=Roboto:wght@400&family=Work+Sans:wght@400&display=swap" rel="stylesheet">
<style>
  :root {
    --navy: #143a69;
    --sky: #0fa3e6;
    --ink: #1d3557;
    --paper: #ffffff;
    --backdrop: #2a2a2a;
  }
  * { margin: 0; padding: 0; box-sizing: border-box; }
  html, body {
    width: 1200px; height: 900px; overflow: hidden;
    background: var(--backdrop);
  }
  .canvas { position: relative; width: 1200px; height: 900px; }

  .card {
    position: absolute; left: 261px; width: 656px; height: 358px;
    box-shadow: 0 4px 14px rgba(0,0,0,0.45);
  }
  .card--front { top: 69px; background: var(--paper); }
  .card--back  { top: 472px; background: var(--navy); }

  .wordmark {
    font-family: "Montserrat", sans-serif; font-weight: 600;
    letter-spacing: 0.02em; line-height: 1.1; text-transform: uppercase;
  }
  .card--front .wordmark {
    position: absolute; left: 31px; top: 150px;
    font-size: 24px; color: var(--navy);
  }
  .card--back .wordmark {
    position: absolute; left: 0; right: 0; top: 120px;
    text-align: center; font-size: 38px; color: #ffffff;
  }

  .person { position: absolute; right: 32px; top: 188px; text-align: right; }
  .person__name {
    font-family: "Roboto", sans-serif; font-size: 26px;
    color: var(--sky); line-height: 1.1;
  }
  .person__title {
    font-family: "Work Sans", sans-serif; font-size: 15px;
    color: var(--ink); margin-top: 3px;
  }

  .divider {
    position: absolute; left: 31px; right: 32px; top: 247px;
    height: 1.5px; background: var(--navy);
  }

  .contact-list {
    position: absolute; left: 31px; top: 273px; list-style: none;
    font-family: "Work Sans", sans-serif; font-size: 15.5px; color: var(--ink);
  }
  .contact-list li { display: flex; align-items: center; height: 21px; }
  .contact-list svg { width: 11px; height: 11px; margin-right: 8px; flex: none; }
  .contact-list .accent { color: var(--sky); }

  .address {
    position: absolute; right: 32px; top: 294px; text-align: right;
    font-family: "Work Sans", sans-serif; font-size: 15.5px; color: var(--ink);
    line-height: 21px; font-style: normal;
  }
</style>
</head>
<body>
<main class="canvas">
  <section class="card card--front">
    <div class="wordmark">Harbor Ledger<br>Funds LLC</div>

    <div class="person">
      <div class="person__name">DANIEL WHITFORD</div>
      <div class="person__title">Director</div>
    </div>

    <div class="divider"></div>

    <ul class="contact-list">
      <li>
        <svg viewBox="0 0 12 12" aria-hidden="true"><path d="M3 1 L5 3.5 L4 5 Q5.5 7.5 7.5 8.5 L9 7.5 L11 9.5 L9.5 11 Q5 10.5 1.5 4.5 Z" fill="#0fa3e6"/></svg>
        +330 5718-4206
      </li>
      <li>
        <svg viewBox="0 0 12 12" aria-hidden="true"><rect x="1" y="2.5" width="10" height="7" fill="none" stroke="#0fa3e6" stroke-width="1.2"/><path d="M1 2.5 L6 6.5 L11 2.5" fill="none" stroke="#0fa3e6" stroke-width="1.2"/></svg>
        info@harborledgerfunds.com
      </li>
      <li>
        <svg viewBox="0 0 12 12" aria-hidden="true"><circle cx="6" cy="6" r="5" fill="none" stroke="#0fa3e6" stroke-width="1"/><ellipse cx="6" cy="6" rx="2.2" ry="5" fill="none" stroke="#0fa3e6" stroke-width="0.9"/><path d="M1 6 H11 M2 3.5 H10 M2 8.5 H10" stroke="#0fa3e6" stroke-width="0.8"/></svg>
        <span>www.<span class="accent">harborledgerfunds</span>.com</span>
      </li>
    </ul>

    <address class="address">
      1187 Larkspur Lane<br>
      Cedar Hollow, CA 95412
    </address>
  </section>

  <section class="card card--back">
    <div class="wordmark">Harbor Ledger<br>Funds LLC</div>
  </section>
</main>
</body>
</html>
```